Meridale Bed Company Needs Business Card

Looking for a very nice looking business card. Creative but not extravagant. We sell beds and pillows across the U.S. and need something professional but catchy. I have attached the logo.

Name : Devin Holt
Title : President
Phone : (800) 471-2960
Email: sleep@quilmora.com
Website: www.quilmora.com

Can be single-sided or double-sided
horizontal or vertical

Can use Blues/Greys

Target Market(s)

Mass Market

Industry/Entity Type

Retail

Contact Information for Business Card

Name : Devin Holt
Title : President
Phone : (800) 471-2960
Email: sleep@quilmora.com
Website: www.quilmora.com

Requirements
Must have
• Clean, Modern, Smooth
• Can use Blues/Greys
• On the other side without the information - have something simple like www.quilmora.com or our logo
Nice to have
• Surprise me
Should not have
• Nothing crazy, nothing cluttered

```html
<!DOCTYPE html>
<html lang="en">
<head>
<meta charset="utf-8">
<title>Meridale Bed Company – Business Card</title>
<link rel="stylesheet" href="https://fonts.googleapis.com/css2?family=Arimo:wght@400;700&display=swap">
<style>
  :root {
    --page-bg: #d9d7d4;
    --card-bg: #1b1c1e;
    --brand-blue: #2a9fd6;
    --text-light: #e6e7e8;
    --text-muted: #c9cacc;
    --divider: #8a8c90;
  }
  * { margin: 0; padding: 0; box-sizing: border-box; }
  html, body {
    width: 1200px;
    height: 787px;
    overflow: hidden;
    background: var(--page-bg);
  }
  .canvas {
    position: relative;
    width: 1200px;
    height: 787px;
    display: flex;
    align-items: center;
    justify-content: center;
    gap: 40px;
  }
  .card {
    width: 520px;
    height: 297px;
    background: var(--card-bg);
    border-radius: 3px;
    box-shadow: 0 10px 28px rgba(0,0,0,0.28);
    position: relative;
    overflow: hidden;
  }
  .brand-name {
    font-family: "Arimo", sans-serif;
    font-weight: 400;
    line-height: 1;
    color: var(--brand-blue);
    white-space: nowrap;
  }

  /* Back side */
  .card-back {
    display: flex;
    flex-direction: column;
    align-items: center;
    justify-content: center;
  }
  .card-back .brand-name {
    font-size: 76px;
  }
  .card-back .web-line {
    margin-top: 28px;
    font-family: "Arimo", sans-serif;
    font-weight: 400;
    font-size: 13px;
    letter-spacing: 6px;
    color: var(--text-muted);
  }

  /* Front side */
  .card-front {
    display: flex;
    align-items: center;
    padding: 0 24px 0 36px;
  }
  .card-front .brand-name {
    font-size: 46px;
    width: 230px;
  }
  .divider {
    width: 1px;
    height: 150px;
    margin: 0 22px 0 16px;
    background: linear-gradient(to bottom, transparent, var(--divider) 25%, var(--divider) 75%, transparent);
  }
  .contact {
    font-family: "Arimo", sans-serif;
    color: var(--text-light);
  }
  .contact .person-name {
    font-weight: 700;
    font-size: 19px;
    color: var(--brand-blue);
  }
  .contact .person-title {
    font-size: 15px;
    margin-top: 2px;
    margin-bottom: 12px;
  }
  .contact-list { list-style: none; }
  .contact-list li {
    display: flex;
    align-items: center;
    gap: 8px;
    font-size: 14px;
    line-height: 1.6;
    white-space: nowrap;
  }
  .contact-list svg {
    width: 14px;
    height: 14px;
    flex: none;
    fill: var(--brand-blue);
  }
</style>
</head>
<body>
<main class="canvas">
  <section class="card card-back" aria-label="Card back">
    <div class="brand-name">quilmora</div>
    <div class="web-line">www.quilmora.com</div>
  </section>

  <section class="card card-front" aria-label="Card front">
    <div class="brand-name">quilmora</div>
    <div class="divider"></div>
    <div class="contact">
      <div class="person-name">Devin Holt</div>
      <div class="person-title">President</div>
      <ul class="contact-list">
        <li>
          <svg viewBox="0 0 16 16" aria-hidden="true"><path d="M1 5c0-2 2-3 7-3s7 1 7 3v1h-3.5V4.5h-7V6H1zM4 8l2-2h4l2 2 1 6H3zm4 1.2a2 2 0 1 0 0 4 2 2 0 0 0 0-4z"/></svg>
          <span>(800) 471-2960</span>
        </li>
        <li>
          <svg viewBox="0 0 16 16" aria-hidden="true"><path d="M1 3h14v1.2L8 9 1 4.2zM1 6l7 4.8L15 6v7H1z"/></svg>
          <span>sleep@quilmora.com</span>
        </li>
        <li>
          <svg viewBox="0 0 16 16" aria-hidden="true"><circle cx="8" cy="8" r="7"/><circle cx="8" cy="6.5" r="2.2" fill="#1b1c1e"/><path d="M4 13c1-2.2 2.3-3 4-3s3 .8 4 3z" fill="#1b1c1e"/></svg>
          <span>www.quilmora.com</span>
        </li>
      </ul>
    </div>
  </section>
</main>
</body>
</html>
```